Seed Oil Safety Card for Healthy Restaurant Dining

I am seeking a design for a physical card to communicate my wife's health-related dietary restriction regarding seed oils. This card will be given to restaurant waiters to ensure her meals are prepared without seed oils, as it is a health issue and not merely a preference.
My wife cannot eat any “seed oil” or “processed oil”, including:
- Vegetable oil
- Canola oil
- Soybean oil
- Sunflower oil
- Corn oil
- Cottonseed oil
- Safflower oil
- Peanut oil
- Sesame oil
Oils that are OK for her to consume:
- Butter (most preferable)
- Extra virgin olive oil
- Avocado oil
- Coconut oil
- Ghee
- Lard
- Any other animal-based fats
Key Design Requirements:
- Clarity and speed of communication: The card should be easily read and understood by waiters, even in low-light environments, emphasizing that it's a health concern.
- Avoid common misconceptions: Ensure the design doesn't imply common dietary preferences like "vegetarian" or "no butter." Animal fats and butter are actually preferable for her!
- Preferred term: Use "seed oils" as the term to describe what she cannot eat due to her health issue.
- Trace amounts are acceptable: Communicate that it's OK to use cookware that has previously been in contact with seed oils, but not to have seed oil as an ingredient. Please suggest a concise way to convey this.
- Card dimensions: Design should be 3.5” x 2.25” (standard credit-card size on printorvale.example). Horizontal or vertical layouts are both fine, whichever makes the message clearer.
Design Suggestions:
- Utilize bold and easy-to-read typography to communicate the main message.
- Consider incorporating relevant icons or graphics that help convey the message without adding confusion.
- Use contrasting colors to enhance readability, especially in low-light situations.
- To communicate the “trace amounts OK” part, consider phrases such as:
- "Cross-contamination acceptable"
- “Used cookware OK, no ingredient use”
- “Separate cookware not necessary”
Thank you for your assistance in creating this essential card for my wife's health and safety when dining out!

```html
<!DOCTYPE html>
<html lang="en">
<head>
<meta charset="UTF-8">
<title>Food Restriction Card</title>
<link rel="stylesheet" href="https://fonts.googleapis.com/css2?family=Anton&family=Archivo+Black&family=Oswald:wght@500;600&family=Saira:wght@600&display=swap">
<style>
  :root {
    --red: #d40000;
    --green: #00b300;
    --ink: #222222;
    --white: #ffffff;
    --band: #1e1e1e;
    --amber: #f5a300;
    --edge: #d6d6d6;
    --page: #ffffff;
  }
  * { box-sizing: border-box; margin: 0; padding: 0; }
  html, body { width: 849px; height: 1200px; overflow: hidden; background: var(--page); }
  .sheet { position: relative; width: 849px; height: 1200px; }

  .card {
    position: absolute;
    left: 75px;
    width: 700px;
    height: 450px;
    border-radius: 22px;
    border: 1.5px solid var(--edge);
    overflow: hidden;
    background: var(--white);
  }
  .card-front { top: 130px; }
  .card-back { top: 630px; }

  .card-title {
    position: absolute;
    left: 0; right: 0;
    text-align: center;
    font-family: "Anton", "Oswald", sans-serif;
    color: var(--red);
    font-size: 62px;
    line-height: 1;
    letter-spacing: 0.5px;
  }
  .card-front .card-title { top: 28px; }

  .panel {
    position: absolute;
    top: 100px;
    width: 302px;
    height: 264px;
    clip-path: polygon(0 0, 100% 0, 100% 86%, 88% 100%, 0 100%);
    color: var(--white);
  }
  .panel-avoid { left: 41px; background: var(--red); }
  .panel-allow { left: 357px; background: var(--green); }

  .panel-icon { position: absolute; left: 20px; top: 18px; width: 64px; height: 40px; }

  .panel-label {
    position: absolute;
    left: 96px; top: 12px;
    width: 182px; height: 52px;
    background: var(--white);
    clip-path: polygon(0 0, 100% 0, 100% 84%, 94% 100%, 0 100%);
    text-align: center;
    padding-top: 3px;
  }
  .panel-label .label-name {
    display: block;
    font-family: "Oswald", sans-serif;
    font-weight: 600;
    font-size: 25px;
    line-height: 30px;
    color: var(--ink);
    transform: scaleX(0.88);
  }
  .panel-label .label-status {
    display: block;
    font-family: "Oswald", sans-serif;
    font-weight: 600;
    font-size: 14px;
    line-height: 15px;
  }
  .panel-avoid .label-status { color: var(--red); }
  .panel-allow .label-status { color: var(--green); }

  .oil-list {
    position: absolute;
    left: 22px;
    list-style: none;
    font-family: "Archivo Black", sans-serif;
    font-size: 15px;
    letter-spacing: 1.6px;
  }
  .panel-avoid .oil-list { top: 76px; line-height: 19.8px; }
  .panel-allow .oil-list { top: 84px; line-height: 22.6px; }
  .oil-list li::before { content: "\2022"; margin-right: 4px; }
  .oil-list .note { font-size: 10px; letter-spacing: 1px; margin-left: 4px; }

  .caution-band {
    position: absolute;
    left: 0; right: 0; bottom: 0;
    height: 64px;
    background: var(--band);
    display: flex;
    align-items: center;
    justify-content: center;
    gap: 14px;
    font-family: "Saira", sans-serif;
    font-weight: 600;
    font-size: 17px;
    color: var(--amber);
    letter-spacing: 0.6px;
  }
  .caution-band svg { width: 30px; height: 26px; }

  .back-photo {
    position: absolute; inset: 0;
    background:
      radial-gradient(ellipse at 50% 60%, #e8a21a 0%, #f1c24a 25%, transparent 55%),
      radial-gradient(ellipse at 80% 20%, #eef0b8 0%, transparent 40%),
      radial-gradient(ellipse at 20% 85%, #d99a2a 0%, transparent 40%),
      linear-gradient(135deg, #e9e6dc 0%, #f4e7b2 40%, #ece9e0 100%);
  }
  .back-band {
    position: absolute;
    left: 0; right: 0;
    top: 165px; height: 116px;
    background: rgba(255, 255, 255, 0.78);
  }
  .card-back .card-title { top: 192px; }
</style>
</head>
<body>
<main class="sheet">

  <section class="card card-front">
    <h1 class="card-title">FOOD RESTRICTION CARD</h1>

    <div class="panel panel-avoid">
      <svg class="panel-icon" viewBox="0 0 64 40" aria-hidden="true">
        <circle cx="14" cy="20" r="11" fill="none" stroke="#fff" stroke-width="2.2"/>
        <path d="M9 15 L19 25 M19 15 L9 25" stroke="#fff" stroke-width="2.2" stroke-linecap="round"/>
        <rect x="30" y="8" width="7" height="15" rx="1.5" fill="#fff"/>
        <path d="M39 8 h14 a4 4 0 0 1 4 4 v10 a3 3 0 0 1 -3 3 h-5 l1 9 a3 3 0 0 1 -5 1 l-6 -12 z" fill="#fff"/>
      </svg>
      <div class="panel-label">
        <span class="label-name">Processed Oil</span>
        <span class="label-status">Not Allowed</span>
      </div>
      <ul class="oil-list">
        <li>Corn oil</li>
        <li>Canola oil</li>
        <li>Peanut oil</li>
        <li>Sesame oil</li>
        <li>Soybean oil</li>
        <li>Safflower oil</li>
        <li>Sunflower oil</li>
        <li>Vegetable oil</li>
        <li>Cottonseed oil</li>
      </ul>
    </div>

    <div class="panel panel-allow">
      <svg class="panel-icon" viewBox="0 0 64 40" aria-hidden="true">
        <circle cx="14" cy="22" r="11" fill="none" stroke="#fff" stroke-width="2.2"/>
        <path d="M8 22 L13 27 L21 17" fill="none" stroke="#fff" stroke-width="2.4" stroke-linecap="round" stroke-linejoin="round"/>
        <rect x="30" y="18" width="7" height="15" rx="1.5" fill="#fff"/>
        <path d="M39 33 h14 a4 4 0 0 0 4 -4 v-10 a3 3 0 0 0 -3 -3 h-5 l1 -9 a3 3 0 0 0 -5 -1 l-6 12 z" fill="#fff"/>
      </svg>
      <div class="panel-label">
        <span class="label-name">Natural Oil</span>
        <span class="label-status">Allowed</span>
      </div>
      <ul class="oil-list">
        <li>Butter<span class="note">(most preferable)</span></li>
        <li>Extra virgin olive oil</li>
        <li>Animal-based fats</li>
        <li>Avocado oil</li>
        <li>Coconut oil</li>
        <li>Lard</li>
        <li>Ghee</li>
      </ul>
    </div>

    <footer class="caution-band">
      <svg viewBox="0 0 30 26" aria-hidden="true">
        <path d="M15 2 L28 24 H2 Z" fill="none" stroke="#f5a300" stroke-width="2" stroke-linejoin="round"/>
        <path d="M15 9 V17" stroke="#f5a300" stroke-width="2.2" stroke-linecap="round"/>
        <circle cx="15" cy="20.5" r="1.3" fill="#f5a300"/>
      </svg>
      <span>Cross-contamination acceptable</span>
    </footer>
  </section>

  <section class="card card-back">
    <div class="back-photo" role="img" aria-label="Photo of plastic bottles of golden cooking oil laid out on a light surface"></div>
    <div class="back-band"></div>
    <h2 class="card-title">FOOD RESTRICTION CARD</h2>
  </section>

</main>
</body>
</html>
```